quickdeedsale.com redesign with wireframes, white space and custom form are very important

Need a new two column design that will convert easily to mobile responsive. Lots of white space. Winning design will probably be based on header area and making the custom form stand out. I want the header to be very much like www.tallgatevk.com except the form not to go up into the header.
Here are some of the websites I really like:
www.birchdwell.com
http://ourplotpurchasedirect.com/
http://kellbrightproperty.com/

We buy homes for cash and close fast. Our target is a home seller who is desperate to sell quickly.
I have uploaded my really ugly wireframe and my logo. I also uploaded my photo for the about us box and a possible photo to use for the header.
The copy on the wireframe is what I will be using except for the about us box.

Here is the exact link for video to frame in the top left box.
https://clipvault.example/Qm38pzrtLa

0592cd
85cae6
eaf1f7
fbee3d
ec1f27

• Everything on wireframe.
• Must use Verdana font and nothing should be smaller than 12 point. Most should be in 14 point. (except maybe inside of form)

```html
<!DOCTYPE html>
<html lang="en">
<head>
<meta charset="utf-8">
<title>quickdeedsale.com – Sell Your Home For Cash</title>
<link rel="stylesheet" href="https://fonts.googleapis.com/css2?family=Cabin:wght@700&family=Montserrat:ital,wght@0,400;0,500;0,600;0,700;1,400&display=swap">
<style>
  :root {
    --brand-red: #ef4a2e;
    --page-bg: #eef1f4;
    --panel-grey: #e9edf0;
    --frame-grey: #e4e8eb;
    --nav-grey: #8b8b8b;
    --ink: #333333;
    --ink-soft: #444444;
    --field-border: #d6dbe0;
    --placeholder: #8f8f8f;
    --rule: #e6e8ea;
    --white: #ffffff;
  }
  * { box-sizing: border-box; margin: 0; padding: 0; }
  html, body { width: 1200px; height: 711px; overflow: hidden; }
  body { background: var(--page-bg); font-family: "Montserrat", Verdana, sans-serif; color: var(--ink); position: relative; }

  .page { position: absolute; left: 97px; top: 0; width: 997px; height: 711px; background: var(--white); border-top: 5px solid var(--brand-red); }

  .brand { position: absolute; left: 40px; top: 62px; display: flex; align-items: center; gap: 5px; font-weight: 700; font-size: 12px; line-height: 14px; color: var(--brand-red); white-space: nowrap; }
  .brand-dot { width: 10px; height: 10px; background: var(--brand-red); border-radius: 50%; flex: none; }

  .main-nav { position: absolute; top: 64px; left: 202px; }
  .main-nav a { position: absolute; white-space: nowrap; font-weight: 600; font-size: 12.6px; color: var(--nav-grey); text-decoration: none; }

  .call-box { position: absolute; right: 63px; top: 33px; text-align: center; font-weight: 600; color: #111; }
  .call-title { font-size: 14px; line-height: 18px; }
  .call-hours { font-size: 12.6px; line-height: 17px; }
  .call-phone { display: flex; align-items: center; justify-content: center; gap: 6px; margin-top: 3px; font-size: 19.5px; font-weight: 700; color: var(--brand-red); letter-spacing: 0.3px; }

  .hero { position: absolute; left: 32px; top: 128px; width: 924px; height: 187px; background: var(--frame-grey); padding: 9px 8px 8px; }
  .hero-photo { width: 100%; height: 170px; background: linear-gradient(180deg, #3c7fc0 0%, #6f97b3 35%, #8d7a5e 62%, #5d4a36 82%, #b9b4a8 100%); display: flex; flex-direction: column; align-items: center; justify-content: center; text-align: center; }
  .hero-title { font-family: "Cabin", Verdana, sans-serif; font-weight: 700; font-size: 46px; line-height: 48px; color: var(--white); text-shadow: 0 2px 4px rgba(0,0,0,0.55); white-space: nowrap; }
  .hero-sub { font-family: "Cabin", Verdana, sans-serif; font-weight: 700; font-size: 36px; line-height: 40px; margin-top: 4px; color: var(--white); text-shadow: 0 2px 4px rgba(0,0,0,0.55); white-space: nowrap; }
  .hero-sub .accent { color: var(--brand-red); }

  .side-tab { position: absolute; left: 1094px; top: 182px; width: 35px; height: 79px; background: var(--brand-red); border-radius: 0 4px 4px 0; display: flex; flex-direction: column; }
  .side-tab span { flex: 1; display: flex; align-items: center; justify-content: center; }
  .side-tab span + span { border-top: 1px solid rgba(255,255,255,0.35); }

  .benefits { position: absolute; left: 47px; top: 359px; width: 470px; }
  .benefits h2 { font-weight: 600; font-size: 18.5px; color: var(--brand-red); margin-bottom: 15px; white-space: nowrap; }
  .benefit-list { list-style: none; margin-left: 6px; width: 453px; }
  .benefit-list li { display: flex; align-items: center; gap: 11px; height: 48px; padding-left: 18px; font-size: 15px; color: var(--ink-soft); border-bottom: 1px solid var(--rule); letter-spacing: 0.2px; white-space: nowrap; }
  .benefit-list li:first-child { height: 36px; padding-bottom: 6px; }
  .benefit-list li:last-child { border-bottom: none; }

  .video-intro { position: absolute; left: 50px; top: 560px; width: 463px; height: 59px; background: var(--panel-grey); padding: 7px 10px; font-size: 16px; line-height: 25px; color: var(--ink-soft); }
  .video-frame { position: absolute; left: 50px; top: 642px; width: 463px; height: 80px; background: var(--panel-grey); padding: 9px 9px 0; }
  .video-still { width: 100%; height: 100%; background: linear-gradient(180deg, #2f6fb8 0%, #4f8cc9 60%, #6a8f6a 100%); }

  .lead-form { position: absolute; left: 591px; top: 354px; width: 344px; height: 360px; background: var(--panel-grey); }
  .lead-form-head { position: relative; height: 52px; background: var(--brand-red); border-radius: 4px 4px 0 0; color: var(--white); display: flex; align-items: center; justify-content: center; font-weight: 600; font-size: 17px; white-space: nowrap; }
  .lead-form-head em { font-family: "Cabin", Verdana, sans-serif; font-weight: 700; font-size: 21px; margin-right: 6px; }
  .lead-form-head::after { content: ""; position: absolute; left: 37px; bottom: -8px; border-left: 7px solid transparent; border-right: 7px solid transparent; border-top: 8px solid var(--brand-red); }
  .lead-form h3 { margin-top: 18px; text-align: center; font-weight: 500; font-size: 18.5px; line-height: 23px; color: #111; }
  .field { position: absolute; left: 19px; width: 305px; height: 35px; background: var(--white); border: 1px solid var(--field-border); padding: 0 12px; display: flex; align-items: center; font-style: italic; font-size: 10.5px; color: var(--placeholder); white-space: nowrap; overflow: hidden; }
  .field .req { color: var(--brand-red); margin-left: 3px; font-style: normal; }
</style>
</head>
<body>
  <div class="page">
    <div class="brand"><span class="brand-dot"></span>quickdeedsale.com</div>

    <nav class="main-nav">
      <a style="left:0">Sell Your Home</a>
      <a style="left:127px">How it Works</a>
      <a style="left:241px">Stop Foreclosure</a>
      <a style="left:377px">Probate</a>
      <a style="left:455px">Contact</a>
    </nav>

    <div class="call-box">
      <div class="call-title">Call Us!</div>
      <div class="call-hours">Nights and Weekends ok</div>
      <div class="call-phone">
        <svg width="16" height="16" viewBox="0 0 16 16" aria-hidden="true"><circle cx="8" cy="8" r="8" fill="#ef4a2e"/><path d="M5.2 4.2l1.3-.3.8 2-1 .8c.5 1.1 1.2 1.8 2.3 2.3l.8-1 2 .8-.3 1.3c-.2.6-.8.8-1.4.7C7.3 10.3 5.7 8.7 5 6.3c-.2-.6 0-1.2.2-2.1z" fill="#fff"/></svg>
        555-203-7714
      </div>
    </div>

    <section class="hero">
      <div class="hero-photo" role="img" aria-label="Softly blurred photo of a single-storey house under a blue sky">
        <div class="hero-title">Sell Your Home For Cash in 8 Days</div>
        <div class="hero-sub">We Buy Houses <span class="accent">Nationwide</span></div>
      </div>
    </section>

    <section class="benefits">
      <h2>These are the benefits of selling your home to us.</h2>
      <ul class="benefit-list">
        <li><svg width="20" height="20" viewBox="0 0 20 20" aria-hidden="true"><circle cx="10" cy="10" r="10" fill="#ef4a2e"/><path d="M5.5 10.2l3 3 6-6.5" stroke="#fff" stroke-width="2.4" fill="none" stroke-linecap="round" stroke-linejoin="round"/></svg>You pick the closing date</li>
        <li><svg width="20" height="20" viewBox="0 0 20 20" aria-hidden="true"><circle cx="10" cy="10" r="10" fill="#ef4a2e"/><path d="M5.5 10.2l3 3 6-6.5" stroke="#fff" stroke-width="2.4" fill="none" stroke-linecap="round" stroke-linejoin="round"/></svg>You pay NO commissions or fees</li>
        <li><svg width="20" height="20" viewBox="0 0 20 20" aria-hidden="true"><circle cx="10" cy="10" r="10" fill="#ef4a2e"/><path d="M5.5 10.2l3 3 6-6.5" stroke="#fff" stroke-width="2.4" fill="none" stroke-linecap="round" stroke-linejoin="round"/></svg>You don’t have to paint, clean or make repairs</li>
      </ul>
    </section>

    <div class="video-intro">Watch to see our president Marcus explain how easy it is to sell to us.</div>
    <div class="video-frame">
      <div class="video-still" role="img" aria-label="Video still of a house with trees against a blue sky"></div>
    </div>

    <form class="lead-form">
      <div class="lead-form-head"><em>Yes!</em> I want to sell my home fast!</div>
      <h3>Get a no obligation written offer<br>in 36 hours...</h3>
      <div class="field" style="top:131px">Your Name<span class="req">*</span></div>
      <div class="field" style="top:175px">Your phone number</div>
      <div class="field" style="top:221px">Your Email Address<span class="req">*</span></div>
      <div class="field" style="top:269px">Property Address including City, State and Zip Code<span class="req">*</span></div>
      <div class="field" style="top:314px">Repairs needed if any</div>
    </form>
  </div>

  <div class="side-tab">
    <span><svg width="16" height="16" viewBox="0 0 16 16" aria-hidden="true"><circle cx="8" cy="8" r="7.5" fill="#fff"/><path d="M5.2 4.2l1.3-.3.8 2-1 .8c.5 1.1 1.2 1.8 2.3 2.3l.8-1 2 .8-.3 1.3c-.2.6-.8.8-1.4.7C7.3 10.3 5.7 8.7 5 6.3c-.2-.6 0-1.2.2-2.1z" fill="#ef4a2e"/></svg></span>
    <span><svg width="16" height="12" viewBox="0 0 16 12" aria-hidden="true"><rect width="16" height="12" rx="1.5" fill="#fff"/><path d="M1 1.5l7 5 7-5" stroke="#ef4a2e" stroke-width="1.4" fill="none"/></svg></span>
  </div>
</body>
</html>
```